Brand New Product Needs Sales Focused Website Design

Looking for design of Homepage, Category Page & Product Page for single product sales focused website. TrundleCrate manufacture and distribute a brand new product to the market called PalTote-Case which is a super strong, re-useable, folding & stacking plastic box which can be seen on our current website www.paltote-case.example PalTote-Case was originally developed as an alternative to supermarket carrier bags and was pitched as a box for life against the other low end re-useable products. The original version was made from recycled plastic and pitched very much as environmental product. We are now taking a different direction and have re-designed the boxes in 5 bright and fashionable designs and although we still want the primary focus to be supermarket shopping we want to position the product as a design led, must have shopping and household accessory rather than a boring, cheap looking black plastic box. The new designs will still have the environmental benefits of being able to be re-used thousands of times and being 100% recyclable and save on the imminent 5p tax on carrier bags in the UK however the new designs will not be made from recycled material. Although the main use for PalTote-Case is supermarket shopping it has a multitude of other uses especially where you need temporary storage - laundry, back of the car, moving house/students, gardening, days out, home office filing (will take A4 file), recycling and much more - PalTote-Case is made out of super strong Polypropylene and can be easily washed and sanitised after use and can be folded and unfolded thousands of times and so will last for many years. PalTote-Case is a product that needs to be seen in action to be understood so the web design must quickly and easily communicate what PalTote-Case is and how it works - this can be done with video, images and copy. Our current website does not work for many reasons:- it is too busy, has too much information, tries too hard and ultimately isn't working. Any of the images off our current website can be supplied for use. Once the concept of the website is agreed I can get these photoshopped with the new designs. Pictures of new designs for reference will be attached to this brief. Ultimately we want the website to convert visitors to sales and therefore designers with a proven track record in this field are especially welcome to enter. We also have a Dropbox folder with over 100 product and situation images in - please send email address and we will send an invite to the folder. Due to Christmas period this competition will be run over 15 days however we may choose to extend the deadline to account for the non working days. Any questions feel free to ask - we will respond within 24 hours where possible.

```html
<!DOCTYPE html>
<html lang="en">
<head>
<meta charset="utf-8">
<title>PalTote-Case — Home</title>
<link href="https://fonts.googleapis.com/css2?family=Kaushan+Script&family=Open+Sans:wght@400;600;700&display=swap" rel="stylesheet">
<style>
:root{
  --blue:#1a9fd6;
  --blue-dark:#0f86bd;
  --sky:#bfe9f8;
  --sky-light:#e4f6fd;
  --header-bg:#f4f5f6;
  --ink:#1f1f1f;
  --muted:#8a9aa5;
  --white:#ffffff;
  --footer-bg:#f2f5f7;
}
*{margin:0;padding:0;box-sizing:border-box}
html,body{width:1200px;height:2270px;overflow:hidden}
body{position:relative;font-family:"Open Sans",Arial,sans-serif;color:var(--ink);background:var(--white)}
.abs{position:absolute}
.script{font-family:"Kaushan Script",cursive}

/* header */
.site-header{left:0;top:0;width:1200px;height:97px;background:var(--header-bg);border-top:4px solid var(--blue)}
.brand{left:206px;top:14px;display:flex;align-items:center;gap:10px;font-weight:700;font-size:30px;color:var(--blue);letter-spacing:.5px}
.brand-mark{width:30px;height:30px;background:var(--blue);border-radius:4px}
.header-phone{left:695px;top:16px;font-size:13px;display:flex;align-items:center;gap:8px}
.header-bag{left:843px;top:16px;font-size:13px;display:flex;align-items:center;gap:8px}
.main-nav{left:432px;top:62px;display:flex;gap:22px;font-size:15px}
.main-nav a{color:var(--ink);text-decoration:none;padding-bottom:4px}
.main-nav a.active{border-bottom:2px solid var(--blue)}
.search{left:848px;top:60px;width:144px;height:25px;display:flex}
.search-field{flex:1;border:2px solid var(--blue);background:var(--white)}
.search-btn{width:30px;background:var(--blue);display:flex;align-items:center;justify-content:center}

/* hero */
.hero{left:0;top:97px;width:1200px;height:405px;background:linear-gradient(180deg,#eef9fe 0%,var(--sky) 100%)}
.hero-title{left:208px;top:160px;font-size:25px;font-weight:400;color:#3b3b3b}
.hero-text{left:208px;top:198px;width:318px;font-size:15px;line-height:20px;color:var(--muted)}
.btn{display:flex;align-items:center;justify-content:center;background:var(--blue);color:var(--white);font-weight:600;border-radius:3px;text-decoration:none}
.hero-btn{left:208px;top:360px;width:110px;height:36px;font-size:15px}
.hero-visual{left:548px;top:116px;width:560px;height:320px;border-radius:6px;background:linear-gradient(90deg,#5b8fc4 0%,#7aa6d2 50%,#b8643a 72%,#e9dfc6 100%)}
.slider-dots{left:545px;top:470px;display:flex;gap:12px}
.slider-dots span{width:11px;height:11px;border-radius:50%;background:#1d2a33}
.slider-dots span.on{background:transparent;border:2px solid var(--blue)}

/* section headings */
.section-head{left:200px;width:800px;display:flex;align-items:center;gap:14px}
.section-head::before,.section-head::after{content:"";flex:1;border-top:2px dashed #333}
.section-head h2{font-family:"Kaushan Script",cursive;font-weight:400;font-size:22px;color:#111}
.section-head.dotted::before,.section-head.dotted::after{border-top-style:dotted;border-top-width:3px}

/* how it works */
.how-sub{left:0;width:1200px;top:576px;text-align:center;font-size:15px;font-weight:400}
.step{top:622px;width:144px;text-align:center}
.step-label{color:var(--blue);font-size:15px;margin-bottom:8px}
.step-frame{width:144px;height:126px;border:2px solid var(--blue);padding:5px}
.step-photo{width:100%;height:100%;background:linear-gradient(180deg,#e9eef6,#2a55c9)}
.step-caption{margin-top:16px;font-size:15px}

/* why section */
.why{left:0;top:853px;width:1200px;height:469px;background-color:var(--sky);background-image:radial-gradient(#a6dcf0 1px,transparent 1.3px);background-size:14px 14px}
.feature{width:240px;text-align:center}
.feature-icon{width:114px;height:114px;margin:0 auto;border-radius:50%;background:var(--blue);border:4px solid var(--white);box-shadow:0 0 0 2px var(--blue);display:flex;align-items:center;justify-content:center}
.feature-name{margin-top:8px;font-size:18px;font-weight:600}

/* products */
.product{top:1400px;width:118px;text-align:center}
.product-photo{width:118px;height:95px;border-radius:6px}
.product-name{margin-top:12px;font-size:13px}
.product-price{margin-top:4px;font-size:14px;display:flex;justify-content:center;gap:14px}
.product-price s{color:#444}
.add-cart{margin-top:10px;height:24px;font-size:13px}

/* testimonial */
.testimonials{left:0;top:1625px;width:1200px;height:370px;background-color:var(--sky);background-image:radial-gradient(#a6dcf0 1px,transparent 1.3px);background-size:14px 14px}
.avatar{left:235px;top:1708px;width:136px;height:136px;border-radius:50%;background:linear-gradient(180deg,#f3efe9,#3a3331);border:4px solid var(--white)}
.customer-name{left:200px;top:1850px;width:206px;text-align:center;font-weight:600;font-size:15px}
.quote-box{left:422px;top:1708px;width:540px;height:182px;border:1.5px solid #8fb2c4;border-radius:4px;background:var(--sky-light);padding:22px 16px 0 20px;font-size:11.6px;line-height:20px;color:var(--muted)}
.quote-box::before{content:"";position:absolute;left:-11px;top:108px;width:20px;height:20px;background:var(--sky-light);border-left:1.5px solid #8fb2c4;border-bottom:1.5px solid #8fb2c4;transform:rotate(45deg)}
.quote-mark{position:absolute;left:8px;top:4px;font-size:46px;line-height:46px;color:#c5d3dc;font-family:Georgia,serif}
.view-more{left:543px;top:1925px;width:113px;height:34px;font-size:15px}

/* footer */
.site-footer{left:0;top:1995px;width:1200px;height:227px;background:var(--footer-bg)}
.footer-head{font-size:18px;color:var(--blue);font-weight:600;letter-spacing:.5px}
.quick-links{left:250px;top:2020px}
.quick-links ul{list-style:none;margin-top:18px;padding-left:4px}
.quick-links li{font-size:13px;line-height:27px}
.footer-rule{top:2030px;width:2px;height:170px;background:var(--blue)}
.contact{left:432px;top:2020px}
.contact-row{display:flex;align-items:center;gap:14px;font-size:12.5px;line-height:20px;margin-top:18px}
.follow{left:782px;top:2020px}
.social{display:flex;gap:10px;margin-top:20px}
.social span{width:32px;height:32px;border-radius:3px}
.bottom-bar{left:0;top:2222px;width:1200px;height:48px;background:var(--blue);color:var(--white);font-size:13px}
.copyright{position:absolute;left:222px;top:14px}
.cards{position:absolute;left:815px;top:12px;display:flex;gap:6px}
.cards span{width:36px;height:24px;border-radius:3px;background:var(--white)}
</style>
</head>
<body>

<header class="site-header abs">
  <div class="brand abs"><span class="brand-mark"></span>PalTote-Case</div>
  <div class="header-phone abs">
    <svg width="12" height="14" viewBox="0 0 12 14"><path d="M2 1 L5 1 L6 4 L4 5 Q5 8 7.5 10 L9 8 L12 9 L12 12 Q11 14 8 13 Q2 10 1 4 Z" fill="#1a9fd6"/></svg>
    +44-100-555-0199
  </div>
  <div class="header-bag abs">
    <svg width="14" height="18" viewBox="0 0 14 18"><rect x="1" y="5" width="12" height="12" rx="1" fill="#1a9fd6"/><path d="M4 6 V3 Q7 0 10 3 V6" stroke="#1a9fd6" fill="none" stroke-width="1.5"/></svg>
    My shopping bag (0)
  </div>
  <nav class="main-nav abs">
    <a class="active" href="#">Home</a><a href="#">Category</a><a href="#">Products</a><a href="#">Gurantee</a><a href="#">Contact Us</a>
  </nav>
  <div class="search abs">
    <div class="search-field"></div>
    <div class="search-btn"><svg width="14" height="14" viewBox="0 0 14 14"><circle cx="6" cy="6" r="4.2" stroke="#fff" stroke-width="2" fill="none"/><path d="M9 9 L13 13" stroke="#fff" stroke-width="2"/></svg></div>
  </div>
</header>

<section class="hero abs"></section>
<h1 class="hero-title abs script">Welcome To PALTOTE-CASE</h1>
<p class="hero-text abs">Lorem Ipsum is simply dummy text of the printing and typesetting industry. Lorem Ipsum has been the industry's standard dummy text ever since the 1500s, when an unknown printer took a galley of type and scrambled it to make a type specimen book. It has survived not only five centuries</p>
<a class="btn hero-btn abs" href="#">Read More</a>
<div class="hero-visual abs" role="img" aria-label="Three satchel-style folding cases in blue, tan leather and floral print"></div>
<div class="slider-dots abs"><span class="on"></span><span></span><span></span><span></span><span></span></div>

<div class="section-head abs" style="top:534px"><h2>How It Works</h2></div>
<p class="how-sub abs">From Featherlight Flat-Pack To Rigid Stacking Box In Seconds!</p>

<div class="step abs" style="left:208px"><div class="step-label">Step-1</div><div class="step-frame"><div class="step-photo" role="img" aria-label="Hand holding the folded blue case"></div></div><div class="step-caption">Folded</div></div>
<div class="step abs" style="left:368px"><div class="step-label">Step-2</div><div class="step-frame"><div class="step-photo" role="img" aria-label="Hands opening the clip of the case"></div></div><div class="step-caption">Open The Clip</div></div>
<div class="step abs" style="left:528px"><div class="step-label">Step-3</div><div class="step-frame"><div class="step-photo" role="img" aria-label="Hands pulling out the ends of the case"></div></div><div class="step-caption">Pull Out Ends</div></div>
<div class="step abs" style="left:688px"><div class="step-label">Step-4</div><div class="step-frame"><div class="step-photo" role="img" aria-label="Hands sliding the rails to lock the box"></div></div><div class="step-caption">Slide Rails To Lock</div></div>
<div class="step abs" style="left:848px"><div class="step-label">Step-5</div><div class="step-frame"><div class="step-photo" role="img" aria-label="Two assembled boxes stacked"></div></div><div class="step-caption">Stacks Too!</div></div>

<section class="why abs"></section>
<div class="section-head abs" style="top:877px"><h2>Why PalTote-Case</h2></div>

<div class="feature abs" style="left:225px;top:941px">
  <div class="feature-icon"><svg width="64" height="64" viewBox="0 0 64 64" fill="none" stroke="#fff" stroke-width="7"><path d="M12 30 A20 20 0 0 1 48 20"/><path d="M52 34 A20 20 0 0 1 16 44"/><path d="M40 14 L52 18 L48 30 Z" fill="#fff" stroke-width="2"/><path d="M24 50 L12 46 L16 34 Z" fill="#fff" stroke-width="2"/></svg></div>
  <div class="feature-name">Reusable</div>
</div>
<div class="feature abs" style="left:481px;top:941px">
  <div class="feature-icon"><svg width="60" height="66" viewBox="0 0 60 66" fill="#fff"><rect x="27" y="36" width="6" height="28"/><circle cx="30" cy="12" r="6"/><circle cx="16" cy="20" r="6"/><circle cx="44" cy="20" r="6"/><circle cx="10" cy="34" r="5"/><circle cx="50" cy="34" r="5"/><circle cx="22" cy="32" r="5"/><circle cx="38" cy="32" r="5"/><circle cx="30" cy="24" r="5"/></svg></div>
  <div class="feature-name">Eco Friendly Product</div>
</div>
<div class="feature abs" style="left:737px;top:941px">
  <div class="feature-icon"><svg width="64" height="60" viewBox="0 0 64 60" fill="#fff"><path d="M32 4 L44 24 L36 24 L32 17 L26 27 L18 22 Z"/><path d="M50 30 L60 48 L48 56 L44 50 L52 48 L46 36 Z"/><path d="M6 40 L14 54 L38 54 L38 46 L20 46 L24 40 Z"/></svg></div>
  <div class="feature-name">Recycle</div>
</div>
<div class="feature abs" style="left:225px;top:1136px">
  <div class="feature-icon"><svg width="66" height="56" viewBox="0 0 66 56" fill="none" stroke="#fff" stroke-width="5" stroke-linejoin="round"><path d="M4 18 L14 52 L52 52 L62 18"/><path d="M10 18 Q18 12 26 18 T42 18 T58 18"/><path d="M24 40 L34 28 L44 36" stroke-width="4"/></svg></div>
  <div class="feature-name">Easy Washable</div>
</div>
<div class="feature abs" style="left:481px;top:1136px">
  <div class="feature-icon"><svg width="60" height="60" viewBox="0 0 60 60" fill="none" stroke="#fff" stroke-width="6"><rect x="6" y="28" width="26" height="14" rx="7" transform="rotate(-45 19 35)"/><rect x="28" y="18" width="26" height="14" rx="7" transform="rotate(-45 41 25)"/></svg></div>
  <div class="feature-name">Super Strong</div>
</div>
<div class="feature abs" style="left:737px;top:1136px">
  <div class="feature-icon"><svg width="64" height="56" viewBox="0 0 64 56" fill="none" stroke="#fff" stroke-width="5" stroke-linejoin="round"><path d="M4 10 L22 4 L42 12 L60 6 L60 46 L42 52 L22 44 L4 50 Z"/><path d="M22 4 L22 44 M42 12 L42 52"/></svg></div>
  <div class="feature-name">Foldable</div>
</div>

<div class="section-head dotted abs" style="top:1352px"><h2>Our Products</h2></div>

<div class="product abs" style="left:223px"><div class="product-photo" role="img" aria-label="Tan leather case" style="background:linear-gradient(180deg,#c8713f,#9a4e26)"></div><div class="product-name">PalTote case1</div><div class="product-price"><s>$40.24</s><span>$25.24</span></div><a class="btn add-cart" href="#">ADD TO CART</a></div>
<div class="product abs" style="left:380px"><div class="product-photo" role="img" aria-label="Blue leather case" style="background:linear-gradient(180deg,#6d9fd0,#3f73a8)"></div><div class="product-name">PalTote case1</div><div class="product-price"><s>$40.24</s><span>$25.24</span></div><a class="btn add-cart" href="#">ADD TO CART</a></div>
<div class="product abs" style="left:540px"><div class="product-photo" role="img" aria-label="Woven wicker-pattern case" style="background:linear-gradient(180deg,#6b4a35,#d1b48e)"></div><div class="product-name">PalTote case1</div><div class="product-price"><s>$40.24</s><span>$25.24</span></div><a class="btn add-cart" href="#">ADD TO CART</a></div>
<div class="product abs" style="left:700px"><div class="product-photo" role="img" aria-label="Red and leopard-print case" style="background:linear-gradient(180deg,#8e1d2a,#c79a45)"></div><div class="product-name">PalTote case1</div><div class="product-price"><s>$40.24</s><span>$25.24</span></div><a class="btn add-cart" href="#">ADD TO CART</a></div>
<div class="product abs" style="left:857px"><div class="product-photo" role="img" aria-label="Floral print case" style="background:linear-gradient(180deg,#ead9bf,#8fb8a6)"></div><div class="product-name">PalTote case1</div><div class="product-price"><s>$40.24</s><span>$25.24</span></div><a class="btn add-cart" href="#">ADD TO CART</a></div>

<section class="testimonials abs"></section>
<div class="section-head dotted abs" style="top:1658px"><h2>What Our Customer Says</h2></div>
<div class="avatar abs" role="img" aria-label="Customer portrait"></div>
<div class="customer-name abs">JUNE ARDEN LOWE</div>
<blockquote class="quote-box abs"><span class="quote-mark">“</span>Lorem Ipsum is simply dummy text of the printing and typesetting industry. Lorem Ipsum has been the industry's standard dummy text ever since the 1500s, when an unknown printer took a galley of type and scrambled it to make a type specimen book. It has survived not only five centuries, but also the leap into electronic typesetting, remaining essentially unchanged. It was popularised in the 1960s with the release of Tessaform sheets containing Lorem Ipsum passages, and more recently with desktop publishing software like Quillset Layout including versions of Lorem Ipsum.</blockquote>
<a class="btn view-more abs" href="#">View More</a>

<footer class="site-footer abs" role="img" aria-label="Faint world map background"></footer>
<div class="quick-links abs">
  <div class="footer-head">Quick Links</div>
  <ul><li>Home</li><li>Products</li><li>Categories</li><li>Gurantee</li><li>Contact Us</li></ul>
</div>
<div class="footer-rule abs" style="left:390px"></div>
<div class="contact abs">
  <div class="footer-head">Contact Us</div>
  <div class="contact-row"><svg width="12" height="16" viewBox="0 0 12 16"><path d="M6 0 A6 6 0 0 1 12 6 C12 10 6 16 6 16 C6 16 0 10 0 6 A6 6 0 0 1 6 0 Z" fill="#1f1f1f"/><circle cx="6" cy="6" r="2.2" fill="#f2f5f7"/></svg><span>Lorem Ipsum is simply dummy text of the<br>printing and typesetting industry. Lorem</span></div>
  <div class="contact-row"><svg width="12" height="14" viewBox="0 0 12 14"><path d="M2 1 L5 1 L6 4 L4 5 Q5 8 7.5 10 L9 8 L12 9 L12 12 Q11 14 8 13 Q2 10 1 4 Z" fill="#1f1f1f"/></svg><span>+44-100-555-0199</span></div>
  <div class="contact-row"><svg width="14" height="12" viewBox="0 0 14 12"><path d="M1 5 L7 1 L13 5 L13 11 L1 11 Z" fill="none" stroke="#1f1f1f" stroke-width="1.6"/><path d="M1 5 L7 8 L13 5" fill="none" stroke="#1f1f1f" stroke-width="1.6"/></svg><span>www.paltote-case.example</span></div>
</div>
<div class="footer-rule abs" style="left:740px"></div>
<div class="follow abs">
  <div class="footer-head">Fallow Us On</div>
  <div class="social"><span style="background:#2fa8e0"></span><span style="background:#d9352b"></span><span style="background:#3a5a99"></span><span style="background:#1a76b0"></span></div>
</div>

<div class="bottom-bar abs">
  <span class="copyright">All Rights Reserved@ 2014www.paltote-case.example</span>
  <div class="cards"><span></span><span></span><span></span><span></span></div>
</div>

</body>
</html>
```